Harbourline Electrical Solutions

On one side. LOGO (underneath:) Commercial Industrial Residential

- NAME & CONTACT DETAILS

Marcus T. Hollings
Project Manager

(Cell icon) (441) 555-0187
(Email icon) hlelectricalsolutions@mailvento.com
(Facebook & Instagram icons )@hlelectricalsolutions

Other side: LOGO - underneath ELECTRICAL CONSTRUCTION & MAINTENANCE . LED LIGHTING & AUTOMATION . LIFE SAFETY SYSTEMS (FIRE ALARM / SECURITY) . DATA & COMMUNICATION

```html
<!DOCTYPE html>
<html lang="en">
<head>
<meta charset="utf-8">
<title>Harbourline Electrical Solutions – Business Card</title>
<link rel="stylesheet" href="https://fonts.googleapis.com/css2?family=Montserrat:wght@400;500;600&display=swap">
<style>
  :root {
    --page: #e9e6e0;
    --card-dark: #4a4a4a;
    --card-light: #ffffff;
    --teal: #1d4e63;
    --ink: #3a3a3a;
    --white: #ffffff;
  }
  * { margin: 0; padding: 0; box-sizing: border-box; }
  html, body { width: 1200px; height: 900px; overflow: hidden; }
  body {
    position: relative;
    background: var(--page);
    font-family: "Montserrat", Arial, sans-serif;
  }
  .card {
    position: absolute;
    left: 311px;
    width: 577px;
    height: 329px;
  }
  .card-back { top: 98px; background: var(--card-dark); color: var(--white); }
  .card-front { top: 472px; background: var(--card-light); color: var(--ink); }

  .back-texture { position: absolute; inset: 0; background: linear-gradient(180deg, #474747, #4d4d4d); }
  .back-brand {
    position: absolute; right: 128px; top: 205px;
    font-size: 17px; font-weight: 600; letter-spacing: 1px; text-transform: uppercase;
  }
  .services {
    position: absolute; left: 0; right: 0; top: 262px;
    text-align: center; list-style: none;
    font-size: 13px; line-height: 16px; letter-spacing: 0.6px; text-transform: uppercase;
  }

  .front-brand {
    position: absolute; left: 30px; top: 40px;
    display: flex; align-items: center; gap: 10px;
    color: var(--teal); font-weight: 500; text-transform: uppercase;
    font-size: 13px; line-height: 14px; letter-spacing: 1.5px;
  }
  .brand-mark { width: 16px; height: 16px; background: var(--teal); }
  .role { position: absolute; right: 34px; top: 170px; font-size: 13px; }
  .person { position: absolute; right: 34px; top: 185px; font-size: 17px; font-weight: 500; color: var(--teal); }
  .sectors {
    position: absolute; left: 30px; right: 36px; top: 210px;
    display: flex; align-items: center; gap: 6px;
    font-size: 13.5px; font-weight: 500; color: var(--teal);
  }
  .sectors::after { content: ""; flex: 1; height: 2px; background: var(--teal); }
  .contact { position: absolute; left: 30px; top: 241px; list-style: none; font-size: 14.5px; }
  .contact li { display: flex; align-items: center; gap: 9px; height: 23px; }
  .contact svg { width: 18px; height: 18px; }
  .social { position: absolute; right: 34px; top: 241px; text-align: right; font-size: 14.5px; }
  .social-dot { display: block; width: 18px; height: 18px; border-radius: 50%; background: var(--teal); margin: 0 0 5px auto; }
</style>
</head>
<body>
  <section class="card card-back">
    <div class="back-texture" role="img" aria-label="Faint repeating brand-name pattern on dark grey"></div>
    <div class="back-brand">Harbourline</div>
    <ul class="services">
      <li>Electrical Construction &amp; Maintenance</li>
      <li>Life Safety Systems (Fire Alarm | Security)</li>
      <li>LED Lighting &amp; Automation &nbsp;|&nbsp; Data &amp; Communication</li>
    </ul>
  </section>

  <section class="card card-front">
    <div class="front-brand">
      <span class="brand-mark"></span>
      <span>Harbourline<br>Electrical<br>Solutions</span>
    </div>
    <p class="role">Project Manager</p>
    <p class="person">Marcus T. Hollings</p>
    <p class="sectors">Commercial Industrial Residential</p>
    <ul class="contact">
      <li>
        <svg viewBox="0 0 18 18" aria-hidden="true"><circle cx="9" cy="9" r="9" fill="#1d4e63"/><rect x="6" y="4" width="6" height="10" rx="1" fill="none" stroke="#fff" stroke-width="1.3"/><circle cx="9" cy="12" r="0.7" fill="#fff"/></svg>
        (441) 555-0187
      </li>
      <li>
        <svg viewBox="0 0 18 18" aria-hidden="true"><circle cx="9" cy="9" r="9" fill="#1d4e63"/><rect x="4.5" y="6" width="9" height="6.5" fill="none" stroke="#fff" stroke-width="1.2"/><path d="M4.5 6 L9 9.8 L13.5 6" fill="none" stroke="#fff" stroke-width="1.2"/></svg>
        hlelectricalsolutions@mailvento.com
      </li>
    </ul>
    <div class="social">
      <span class="social-dot"></span>
      @hlelectricalsolutions
    </div>
  </section>
</body>
</html>
```